Brightmoor Lift Inc Website Deisgn

We are a new small elevator contracting company.
We would like a full website designed similar to
http://pellingtonlifts.com or https://www.northvalelifting.ca/
In addition to contents found on the above webpages.. we would like a section for project gallery etc.... have fun with it ... make it professional

Target Market(s)

Elevator Consultants - Property managers - Condo Boards - Commercial office buildings

Coding

Number of Pages Required

5+ page

Requirements
Must have
• Navigation Bar.. Be view able via mobile ..Should be pictures of Tall Office buildings in background.. Toronto city skyline etc....

Have Fun!

```html
<!DOCTYPE html>
<html lang="en">
<head>
<meta charset="utf-8">
<title>Brightmoor Lift Inc — Website Design</title>
<link href="https://fonts.googleapis.com/css2?family=Poppins:wght@400;500;600;700;800&display=swap" rel="stylesheet">
<style>
:root{
  --red:#c32d42;
  --red-dark:#a92437;
  --navy:#1b1d33;
  --ink:#1a1a1a;
  --text:#555;
  --grey:#ececec;
  --page:#f2f2f2;
  --white:#fff;
  --line:#d8d8d8;
}
*{box-sizing:border-box;margin:0;padding:0}
html,body{width:1200px;height:3436px;overflow:hidden}
body{background:var(--page);font-family:"Poppins",sans-serif;color:var(--ink);position:relative}

.brand-mark{position:absolute;left:0;top:120px;width:1200px;display:flex;justify-content:center;align-items:center;gap:22px}
.brand-mark .dot{width:110px;height:110px;border:12px solid var(--ink);border-radius:50%}
.brand-mark .name{font-size:68px;font-weight:800;color:var(--ink);letter-spacing:-1px}

/* shared */
.photo{display:block}
.ph-night{background:linear-gradient(160deg,#2a2520 0%,#120f0c 45%,#3a2a18 75%,#0d0b0a 100%)}
.ph-bldg{background:linear-gradient(180deg,#5b6b7c,#2a2e36 60%,#8a6a4a)}
.ph-steel{background:linear-gradient(135deg,#8ea0b8,#4d5d74 60%,#a8b3c2)}
.ph-tool{background:linear-gradient(135deg,#3a3a3a,#6b6b6b 45%,#d3343c 60%,#2b2b2b)}
.ph-glass{background:linear-gradient(200deg,#e7ecf2,#6b8db0 40%,#233a5a)}
.ph-city{background:linear-gradient(180deg,#0f2a3a,#1c6a78 45%,#0a1a22)}
.ph-sunset{background:linear-gradient(180deg,#a9c6dc,#c9884e 55%,#5a3320)}
.ph-blue{background:linear-gradient(150deg,#e2a455,#2f6fb0 45%,#0e2544)}
.ph-grey{background:linear-gradient(180deg,#c9ccd0,#3d3f44 50%,#16171a)}
.ph-aerial{background:linear-gradient(180deg,#7e8a92,#4b5359 50%,#a59b8c)}
.ph-dusk{background:linear-gradient(180deg,#2b4a63,#122433 55%,#c08a40)}
.ph-lights{background:linear-gradient(180deg,#0c0f18,#1b2236 55%,#c88b2c)}
.ph-map{background:linear-gradient(135deg,#eef0ec,#e3e7e1 50%,#f4efd8)}

/* ---------- desktop ---------- */
.desktop{position:absolute;left:349px;top:383px;width:766px;height:2894px;background:var(--white);box-shadow:0 2px 14px rgba(0,0,0,.08)}
.d-nav{height:48px;border-top:3px solid var(--navy);display:flex;align-items:center;padding:0 0 0 95px;background:var(--white)}
.d-logo{display:flex;align-items:center;gap:4px;font-size:15px;font-weight:800;color:var(--ink);width:140px}
.d-logo i{width:12px;height:12px;border:2px solid var(--ink);border-radius:50%}
.d-menu{display:flex;gap:19px;font-size:8.5px;color:#333}
.d-cta{margin-left:20px;background:var(--red);color:var(--white);font-size:8.5px;padding:0 18px;height:24px;line-height:24px}

.d-hero{height:377px;position:relative;color:var(--white);text-align:center}
.d-hero .photo{position:absolute;inset:0}
.d-hero .copy{position:relative;padding-top:118px}
.d-hero .kicker{font-size:17px;letter-spacing:1px;font-weight:400}
.d-hero h1{font-size:29px;font-weight:800;line-height:39px;letter-spacing:1px;margin-top:6px}
.btn{display:inline-block;background:var(--red);color:var(--white)}
.d-hero .btn{font-size:9px;width:86px;height:23px;line-height:23px;margin-top:14px}

.sec-title{font-weight:800;text-align:center;color:var(--ink)}
.d .sec-title{font-size:26px}
.lead{text-align:center;color:var(--text)}
.d .lead{font-size:9px;line-height:14px;width:480px;margin:10px auto 0}

.d-about{height:202px;background:var(--grey);padding-top:50px}
.d-about .lead{width:570px}
.d-about .red{color:var(--red)}

.d-services{height:432px;padding-top:48px}
.d-cards{display:flex;gap:15px;margin:22px 0 0 96px}
.card{background:var(--white);box-shadow:0 0 6px rgba(0,0,0,.14);text-align:center}
.d-cards .card{width:181px;height:236px;padding:13px}
.d-cards .photo{height:84px}
.card h3{font-weight:500}
.d-cards h3{font-size:12.5px;margin-top:18px}
.card p{color:var(--text)}
.d-cards p{font-size:8.5px;line-height:13px;margin-top:8px;padding:0 4px}
.card .more{color:var(--red);font-weight:500}
.d-cards .more{font-size:8.5px;margin-top:10px;display:block}

.d-faq{height:441px;background:var(--red);color:var(--white);padding-top:50px}
.d-faq .sec-title,.d-faq .lead{color:var(--white)}
.faq-list{display:flex;flex-direction:column}
.d-faq .faq-list{width:528px;margin:24px 0 0 118px;gap:12px}
.faq{border:1px solid rgba(255,255,255,.75);display:flex;justify-content:space-between;align-items:center}
.d-faq .faq{height:26px;padding:0 14px 0 15px;font-size:8.5px}
.plus{border-radius:50%;background:var(--white);position:relative;flex:none}
.plus::before,.plus::after{content:"";position:absolute;background:var(--red);left:50%;top:50%;transform:translate(-50%,-50%)}
.d-faq .plus{width:12px;height:12px}
.d-faq .plus::before{width:6px;height:1.5px}
.d-faq .plus::after{width:1.5px;height:6px}
.faq.open{display:block}
.d-faq .faq.open{height:91px;padding:14px 15px}
.faq.open .q{display:flex;justify-content:space-between;align-items:center}
.d-faq .open .q{font-size:11px}
.minus{border-radius:50%;background:#e9654a;position:relative;flex:none}
.minus::before{content:"";position:absolute;background:var(--white);left:50%;top:50%;transform:translate(-50%,-50%)}
.d-faq .minus{width:12px;height:12px}
.d-faq .minus::before{width:6px;height:1.5px}
.d-faq .open p{font-size:8.5px;line-height:12.5px;margin-top:8px;width:470px}

.d-gallery{height:743px;padding-top:50px}
.d-grid{display:flex;gap:10px;margin:24px 0 0 118px}
.d-grid .col{display:flex;flex-direction:column;gap:9px;width:169px}

.d-contact{height:576px;background:var(--grey);padding-top:48px}
.d-info{display:flex;gap:20px;margin:26px 0 0 96px}
.info{background:var(--page);text-align:center;display:flex;flex-direction:column;align-items:center}
.d-info .info{width:177px;height:111px;padding-top:24px;font-size:8.5px;line-height:13px;background:#f3f3f3}
.info svg{margin-bottom:12px}
.d-form{margin:13px 0 0 96px;width:574px;height:257px;background:#e6e6e6;display:flex}
.form{display:flex;flex-direction:column}
.d-form .form{width:297px;padding:30px 0 0 30px;gap:8px}
.field{background:var(--white);border:1px solid #bdbdbd;color:#888}
.d-form .field{width:216px;height:20px;font-size:7.5px;padding:4px 10px}
.field.msg{position:relative}
.d-form .field.msg{height:113px}
.send{position:absolute;right:0;bottom:0;background:var(--navy)}
.d-form .send{width:26px;height:26px}
.d-form .photo{width:277px;height:257px}

.footer{background:var(--navy);color:var(--white);display:flex;flex-direction:column;align-items:center}
.d-footer{height:75px;padding-top:17px;font-size:8px}
.socials{display:flex}
.socials span{border-radius:50%;background:#3b8fd9}
.d-footer .socials{gap:9px;margin-bottom:12px}
.d-footer .socials span{width:16px;height:16px}

/* ---------- mobile ---------- */
.mobile{position:absolute;left:85px;top:383px;width:179px;height:2944px;background:var(--white);box-shadow:0 2px 14px rgba(0,0,0,.08)}
.m-nav{height:23px;border-top:2px solid var(--navy);display:flex;justify-content:space-between;align-items:center;padding:0 8px}
.m-logo{display:flex;align-items:center;gap:2px;font-size:7px;font-weight:800}
.m-logo i{width:7px;height:7px;border:1px solid var(--ink);border-radius:50%}
.m-burger{width:11px;height:11px;background:var(--red);display:flex;flex-direction:column;justify-content:center;align-items:center;gap:1.5px}
.m-burger b{width:6px;height:1px;background:var(--white)}
.m-hero{height:224px;position:relative;color:var(--white);text-align:center}
.m-hero .photo{position:absolute;inset:0}
.m-hero .copy{position:relative;padding-top:60px}
.m-hero .kicker{font-size:8px}
.m-hero h1{font-size:13px;font-weight:800;line-height:18px;margin-top:6px;letter-spacing:.3px}
.m-hero .btn{font-size:6px;width:64px;height:16px;line-height:16px;margin-top:10px}
.m .sec-title{font-size:11px}
.m .lead{font-size:6px;line-height:10px;width:150px;margin:10px auto 0}
.m-about{height:200px;background:var(--grey);padding-top:28px}
.m-about .red{color:var(--red)}
.m-services{height:794px;padding-top:28px}
.m-cards{display:flex;flex-direction:column;gap:14px;margin:16px 0 0 9px}
.m-cards .card{width:160px;height:208px;padding:13px 12px}
.m-cards .photo{height:75px}
.m-cards h3{font-size:10px;margin-top:20px}
.m-cards p{font-size:6px;line-height:10px;margin-top:8px;padding:0 10px}
.m-cards .more{font-size:6.5px;margin-top:8px;display:block}
.m-faq{height:443px;background:var(--red);color:var(--white);padding-top:28px}
.m-faq .sec-title,.m-faq .lead{color:var(--white)}
.m-faq .lead{width:160px}
.m-faq .faq-list{width:160px;margin:16px 0 0 9px;gap:9px}
.m-faq .faq{height:40px;padding:0 8px 0 10px;font-size:7px;font-weight:500;line-height:10px}
.m-faq .plus{width:7px;height:7px}
.m-faq .plus::before{width:4px;height:1px}
.m-faq .plus::after{width:1px;height:4px}
.m-faq .faq.open{height:109px;padding:10px}
.m-faq .open .q{font-size:7px;line-height:10px}
.m-faq .minus{width:7px;height:7px}
.m-faq .minus::before{width:4px;height:1px}
.m-faq .open p{font-size:6px;line-height:10px;margin-top:4px}
.m-gallery{height:623px;padding-top:32px}
.m-grid{display:flex;gap:8px;margin:20px 0 0 9px}
.m-grid .col{display:flex;flex-direction:column;gap:8px}
.m-grid .col:first-child{width:75px}
.m-grid .col:last-child{width:77px}
.m-contact{height:560px;background:var(--grey);padding-top:30px}
.m-info{display:flex;flex-direction:column;gap:11px;margin:14px 0 0 9px}
.m-info .info{width:160px;height:64px;padding-top:10px;font-size:6px;line-height:9px}
.m-info .info svg{margin-bottom:6px}
.m-form{margin:12px 0 0 9px;width:160px;height:188px;background:#e6e6e6}
.m-form .form{padding:22px 0 0 13px;gap:9px}
.m-form .field{width:134px;height:20px;font-size:6px;padding:4px 8px}
.m-form .field.msg{height:56px}
.m-form .send{width:22px;height:20px}
.m-footer{height:77px;padding-top:25px;font-size:6px}
.m-footer .socials{gap:8px;margin-bottom:12px}
.m-footer .socials span{width:14px;height:14px}
</style>
</head>
<body>

<div class="brand-mark"><span class="dot"></span><span class="name">BRIGHTMOOR LIFT INC</span></div>

<!-- Mobile layout -->
<section class="mobile m">
  <header class="m-nav"><div class="m-logo"><i></i>BRIGHTMOOR</div><div class="m-burger"><b></b><b></b><b></b></div></header>
  <div class="m-hero">
    <div class="photo ph-night" role="img" aria-label="Toronto office towers at night"></div>
    <div class="copy">
      <p class="kicker">WE ARE TORONTO'S #1 CHOICE FOR</p>
      <h1>Elevator<br>Maintenance, Repair<br>&amp; Modernization</h1>
      <span class="btn">Learn More</span>
    </div>
  </div>
  <div class="m-about">
    <h2 class="sec-title">About Brightmoor Lift</h2>
    <p class="lead"><span class="red">Lorem ipsum dolor sit amet, consectetur an adipiscing elit, sed do eiusmod tempor incididunt ut labore man et dolore magna sed do eiusmod tempor incididunt ut aliqua.</span> Ut enim ad minim veniam, quis monda nostrud monda exercitation ullamco na malaboris nisi ut aliquip ex eab a acommodo consequat. Duis aute irure dolor in manreprehenderit , in voluptate velit esse cillum dolore eu fugiat a nulla pariatur.</p>
  </div>
  <div class="m-services">
    <h2 class="sec-title">Services We Offer</h2>
    <p class="lead">Lorem ipsum dolor sit amet, consectetur an adipiscing elit, sed do eiusmod tempor incididunt ut labore man et dolore magna aliqua.</p>
    <div class="m-cards">
      <div class="card"><div class="photo ph-bldg" role="img" aria-label="Lit office floors at night"></div><h3>Modernization</h3><p>Lorem ipsum dolor sit amet, consectetur adipiscing elit, sed do eiusmod tempor...</p><span class="more">Free Quote</span></div>
      <div class="card"><div class="photo ph-steel" role="img" aria-label="Technician working on a glass facade"></div><h3>Maintenance</h3><p>Lorem ipsum dolor sit amet, consectetur adipiscing elit, sed do eiusmod tempor...</p><span class="more">Free Quote</span></div>
      <div class="card"><div class="photo ph-tool" role="img" aria-label="Red hand tools on a dark surface"></div><h3>Other Services</h3><p>Lorem ipsum dolor sit amet, consectetur adipiscing elit, sed do eiusmod tempor...</p><span class="more">Free Quote</span></div>
    </div>
  </div>
  <div class="m-faq">
    <h2 class="sec-title">Frequently Ask Questions</h2>
    <p class="lead">Lorem ipsum dolor sit amet, consectetur an adipiscing elit, sed do eiusmod tempor incididunt ut labore man et dolore magna aliqua.</p>
    <div class="faq-list">
      <div class="faq open"><div class="q"><span>Lorem ipsum dolor sit amet,<br>consectetur?</span><span class="minus"></span></div><p>Lorem ipsum dolor sit amet, consectetur adipiscing elit, sed do eiusmod tempor incididunt ut labore et dolore magna aliqua. Ut enim ad minim veniam, quis nostrud exercitation ullamco laboris nisi ut aliquip ex ea commodo consequat.</p></div>
      <div class="faq"><span>Lorem ipsum dolor sit amet,<br>consectetur?</span><span class="plus"></span></div>
      <div class="faq"><span>Lorem ipsum dolor sit amet,<br>consectetur?</span><span class="plus"></span></div>
      <div class="faq"><span>Lorem ipsum dolor sit amet,<br>consectetur?</span><span class="plus"></span></div>
      <div class="faq"><span>Lorem ipsum dolor sit amet,<br>consectetur?</span><span class="plus"></span></div>
    </div>
  </div>
  <div class="m-gallery">
    <h2 class="sec-title">Our Project Gallery</h2>
    <p class="lead">Lorem ipsum dolor sit amet, consectetur an adipiscing elit, sed do eiusmod tempor incididunt ut labore man et dolore magna aliqua.</p>
    <div class="m-grid">
      <div class="col">
        <div class="photo ph-glass" style="height:75px" role="img" aria-label="Glass tower from below"></div>
        <div class="photo ph-sunset" style="height:73px" role="img" aria-label="Downtown towers at sunset"></div>
        <div class="photo ph-blue" style="height:125px" role="img" aria-label="Blue glass skyscrapers"></div>
        <div class="photo ph-dusk" style="height:80px" role="img" aria-label="City skyline at dusk"></div>
        <div class="photo ph-dusk" style="height:86px" role="img" aria-label="Aerial city view at dusk"></div>
      </div>
      <div class="col">
        <div class="photo ph-city" style="height:92px" role="img" aria-label="Towers with light trails at night"></div>
        <div class="photo ph-aerial" style="height:73px" role="img" aria-label="Aerial view of city blocks"></div>
        <div class="photo ph-grey" style="height:128px" role="img" aria-label="Black office tower"></div>
        <div class="photo ph-lights" style="height:146px" role="img" aria-label="Building facade with lit floors"></div>
      </div>
    </div>
  </div>
  <div class="m-contact">
    <h2 class="sec-title">Contact Us</h2>
    <p class="lead">Lorem ipsum dolor sit amet, consectetur an adipiscing elit, sed do eiusmod tempor incididunt ut labore man et dolore magna aliqua.</p>
    <div class="m-info">
      <div class="info"><svg width="13" height="15" viewBox="0 0 14 18" fill="none" stroke="#c32d42" stroke-width="1.4"><path d="M7 17s6-6 6-10A6 6 0 0 0 1 7c0 4 6 10 6 10z"/><circle cx="7" cy="7" r="2.2"/></svg>2280 Harlow Ridge<br>Pkwy Fenwick GA 30012</div>
      <div class="info"><svg width="14" height="14" viewBox="0 0 18 18" fill="none" stroke="#c32d42" stroke-width="1.4"><circle cx="9" cy="9" r="8"/><path d="M6 5l2 2-1 1.5a6 6 0 0 0 2.5 2.5L11 10l2 2-1.2 1.2C9 13 5 9 4.8 6.2z"/></svg>Telephone:<br>+00 (0) 00 123 00 56</div>
      <div class="info"><svg width="14" height="11" viewBox="0 0 18 13" fill="none" stroke="#c32d42" stroke-width="1.4"><rect x="1" y="1" width="16" height="11"/><path d="M1 1l8 6 8-6"/></svg>Email:<br>info@brightmoorlift.com</div>
    </div>
    <div class="m-form">
      <div class="form">
        <div class="field">name</div><div class="field">Email</div><div class="field">Problem/Issue</div>
        <div class="field msg">Message<span class="send"></span></div>
      </div>
    </div>
  </div>
  <footer class="footer m-footer"><div class="socials"><span></span><span></span><span></span><span></span></div><p>©2020 all right reserved &nbsp; | &nbsp; privacy policy</p></footer>
</section>

<!-- Desktop layout -->
<section class="desktop d">
  <header class="d-nav">
    <div class="d-logo"><i></i>BRIGHTMOOR</div>
    <nav class="d-menu"><span>Home</span><span>Our Services</span><span>Employees</span><span>FAQs</span><span>Free Quote</span><span>Contact Us</span></nav>
    <span class="d-cta">Free Quote</span>
  </header>
  <div class="d-hero">
    <div class="photo ph-night" role="img" aria-label="Toronto office towers at night"></div>
    <div class="copy">
      <p class="kicker">WE ARE TORONTO'S #1 CHOICE FOR</p>
      <h1>Elevator Maintenance, Repair &amp;<br>Modernization</h1>
      <span class="btn">Learn More</span>
    </div>
  </div>
  <div class="d-about">
    <h2 class="sec-title">About Brightmoor Lift</h2>
    <p class="lead"><span class="red">Lorem ipsum dolor sit amet, consectetur an adipiscing elit, sed do eiusmod tempor incididunt ut labore man et dolore magna sed do eiusmod tempor incididunt ut aliqua.</span><br>Ut enim ad minim veniam, quis monda nostrud monda exercitation ullamco na malaboris nisi ut aliquip ex eab a acommodo consequat. Duis aute irure dolor in manreprehenderit , in voluptate velit esse cillum dolore eu fugiat a nulla pariatur.</p>
  </div>
  <div class="d-services">
    <h2 class="sec-title">Services We Offer</h2>
    <p class="lead">Lorem ipsum dolor sit amet, consectetur an adipiscing elit, sed do eiusmod tempor incididunt ut labore man et dolore magna aliqua.</p>
    <div class="d-cards">
      <div class="card"><div class="photo ph-bldg" role="img" aria-label="Lit office floors at night"></div><h3>Modernization</h3><p>Lorem ipsum dolor sit amet, consectetur adipiscing elit, sed do eiusmod tempor...</p><span class="more">Free Quote</span></div>
      <div class="card"><div class="photo ph-steel" role="img" aria-label="Technician working on a glass facade"></div><h3>Maintenance</h3><p>Lorem ipsum dolor sit amet, consectetur adipiscing elit, sed do eiusmod tempor...</p><span class="more">Free Quote</span></div>
      <div class="card"><div class="photo ph-tool" role="img" aria-label="Red hand tools on a dark surface"></div><h3>Other Services</h3><p>Lorem ipsum dolor sit amet, consectetur adipiscing elit, sed do eiusmod tempor...</p><span class="more">Free Quote</span></div>
    </div>
  </div>
  <div class="d-faq">
    <h2 class="sec-title">Frequently Ask Questions</h2>
    <p class="lead">Lorem ipsum dolor sit amet, consectetur an adipiscing elit, sed do eiusmod tempor incididunt ut labore man et dolore magna aliqua.</p>
    <div class="faq-list">
      <div class="faq open"><div class="q"><span>Lorem ipsum dolor sit amet, consectetur?</span><span class="minus"></span></div><p>Lorem ipsum dolor sit amet, consectetur adipiscing elit, sed do eiusmod tempor incididunt ut labore et dolore magna aliqua. Ut enim ad minim veniam, quis nostrud exercitation ullamco laboris nisi ut aliquip ex ea commodo consequat.</p></div>
      <div class="faq"><span>Lorem ipsum dolor sit amet, consectetur?</span><span class="plus"></span></div>
      <div class="faq"><span>Lorem ipsum dolor sit amet, consectetur?</span><span class="plus"></span></div>
      <div class="faq"><span>Lorem ipsum dolor sit amet, consectetur?</span><span class="plus"></span></div>
      <div class="faq"><span>Lorem ipsum dolor sit amet, consectetur?</span><span class="plus"></span></div>
    </div>
  </div>
  <div class="d-gallery">
    <h2 class="sec-title">Our Project Gallery</h2>
    <p class="lead">Lorem ipsum dolor sit amet, consectetur an adipiscing elit, sed do eiusmod tempor incididunt ut labore man et dolore magna aliqua.</p>
    <div class="d-grid">
      <div class="col">
        <div class="photo ph-glass" style="height:117px" role="img" aria-label="Glass tower from below"></div>
        <div class="photo ph-blue" style="height:216px" role="img" aria-label="Blue glass skyscrapers"></div>
        <div class="photo ph-aerial" style="height:117px" role="img" aria-label="Aerial view of city blocks"></div>
      </div>
      <div class="col">
        <div class="photo ph-city" style="height:203px" role="img" aria-label="Towers with light trails at night"></div>
        <div class="photo ph-grey" style="height:204px" role="img" aria-label="Black office tower"></div>
        <div class="photo ph-lights" style="height:117px" role="img" aria-label="Office tower at night"></div>
      </div>
      <div class="col">
        <div class="photo ph-sunset" style="height:117px" role="img" aria-label="Downtown towers at sunset"></div>
        <div class="photo ph-lights" style="height:204px" role="img" aria-label="Building facade with lit floors"></div>
        <div class="photo ph-dusk" style="height:117px" role="img" aria-label="City skyline at dusk"></div>
      </div>
    </div>
  </div>
  <div class="d-contact">
    <h2 class="sec-title">Contact Us</h2>
    <p class="lead">Lorem ipsum dolor sit amet, consectetur an adipiscing elit, sed do eiusmod tempor incididunt ut labore man et dolore magna aliqua.</p>
    <div class="d-info">
      <div class="info"><svg width="16" height="20" viewBox="0 0 14 18" fill="none" stroke="#c32d42" stroke-width="1.3"><path d="M7 17s6-6 6-10A6 6 0 0 0 1 7c0 4 6 10 6 10z"/><circle cx="7" cy="7" r="2.2"/></svg>2280 Harlow Ridge<br>Pkwy Fenwick GA 30012</div>
      <div class="info"><svg width="19" height="19" viewBox="0 0 18 18" fill="none" stroke="#c32d42" stroke-width="1.3"><circle cx="9" cy="9" r="8"/><path d="M6 5l2 2-1 1.5a6 6 0 0 0 2.5 2.5L11 10l2 2-1.2 1.2C9 13 5 9 4.8 6.2z"/></svg>Telephone:<br>+00 (0) 00 123 00 56</div>
      <div class="info"><svg width="19" height="14" viewBox="0 0 18 13" fill="none" stroke="#c32d42" stroke-width="1.3"><rect x="1" y="1" width="16" height="11"/><path d="M1 1l8 6 8-6"/></svg>Email:<br>info@brightmoorlift.com</div>
    </div>
    <div class="d-form">
      <div class="form">
        <div class="field">name</div><div class="field">email</div><div class="field">Problem/Issue</div>
        <div class="field msg">message<span class="send"></span></div>
      </div>
      <div class="photo ph-map" role="img" aria-label="Street map of the office location"></div>
    </div>
  </div>
  <footer class="footer d-footer"><div class="socials"><span></span><span></span><span></span><span></span></div><p>©2020 all right reserved &nbsp; | &nbsp; privacy policy</p></footer>
</section>

</body>
</html>
```